KLV Plant Services

We are a heavy diesel mechanical business with additional air con certificates, remapping engine rebuilt

Contact Information for Business Card

Company Name, Director Name, Managing Director, Contact details, email and website

Font styles to use
Serif
Script

```html
<!DOCTYPE html>
<html lang="en">
<head>
<meta charset="utf-8">
<title>KLV Plant Services – Business Card</title>
<link rel="stylesheet" href="https://fonts.googleapis.com/css2?family=Roboto:wght@400;700&display=swap">
<style>
  :root {
    --navy: #03065f;
    --ink: #1d1d1f;
    --muted: #6a6a6a;
    --paper: #f5f5f5;
    --backdrop: #e4e4e4;
    --rule: #b9b9b9;
    --white: #ffffff;
  }
  * { box-sizing: border-box; margin: 0; padding: 0; }
  html, body {
    width: 1200px; height: 1040px; overflow: hidden;
    background: var(--backdrop);
    font-family: "Roboto", Arial, sans-serif;
  }
  .card {
    position: absolute; left: 282px;
    width: 644px; height: 368px;
    border-radius: 16px; overflow: hidden;
  }
  .card--front { top: 130px; background: var(--paper); }
  .card--back { top: 567px; background: var(--navy); }

  .brand { position: absolute; font-weight: 700; line-height: 1; }
  .brand__mark { display: block; }
  .brand__sub { display: block; }

  .card--front .brand { left: 118px; top: 150px; color: var(--navy); }
  .card--front .brand__mark { font-size: 50px; letter-spacing: 1px; }
  .card--front .brand__sub { font-size: 17px; margin-top: 4px; }

  .divider {
    position: absolute; left: 324px; top: 98px;
    width: 1px; height: 178px; background: var(--rule);
  }
  .contact { position: absolute; left: 342px; top: 94px; color: var(--ink); }
  .contact__name { font-size: 24px; font-weight: 700; color: var(--navy); line-height: 1.1; }
  .contact__role { font-size: 16px; color: var(--muted); margin-top: 2px; }
  .contact__address { font-size: 16px; line-height: 20px; margin-top: 11px; }
  .contact__list { list-style: none; margin-top: 10px; font-size: 16px; line-height: 20px; }
  .contact__list li { display: flex; align-items: center; gap: 8px; }
  .contact__list svg { width: 14px; height: 14px; fill: var(--navy); flex: none; }

  .edge-rule {
    position: absolute; left: 0; right: 0; top: 344px;
    height: 2px; background: #000;
  }
  .edge-band {
    position: absolute; left: 0; right: 0; top: 350px; bottom: 0;
    background: var(--navy);
  }

  .card--back .brand {
    left: 0; right: 0; top: 122px; text-align: center; color: var(--white);
  }
  .card--back .brand__mark { font-size: 80px; letter-spacing: 2px; }
  .card--back .brand__sub { font-size: 26px; margin-top: 6px; }
</style>
</head>
<body>
  <section class="card card--front">
    <div class="brand">
      <span class="brand__mark">KLV</span>
      <span class="brand__sub">Plant Services</span>
    </div>
    <div class="divider"></div>
    <div class="contact">
      <p class="contact__name">Daniel Hartley</p>
      <p class="contact__role">Managing Director</p>
      <p class="contact__address">4127 Brookfield Avenue<br>Cedar Grove, NY 11020</p>
      <ul class="contact__list">
        <li>
          <svg viewBox="0 0 24 24" aria-hidden="true"><path d="M6.6 10.8a15.1 15.1 0 0 0 6.6 6.6l2.2-2.2c.3-.3.7-.4 1-.2 1.1.4 2.3.6 3.6.6.6 0 1 .4 1 1V20c0 .6-.4 1-1 1A17 17 0 0 1 3 4c0-.6.4-1 1-1h3.5c.6 0 1 .4 1 1 0 1.3.2 2.5.6 3.6.1.3 0 .7-.2 1z"/></svg>
          (555) 0142-7781
        </li>
        <li>
          <svg viewBox="0 0 24 24" aria-hidden="true"><path d="M2 5h20v14H2zm2 2v.5l8 5 8-5V7zm0 2.9V17h16V9.9l-8 5z"/></svg>
          name@KLV.com
        </li>
        <li>
          <svg viewBox="0 0 24 24" aria-hidden="true"><path d="M12 2a10 10 0 1 0 0 20 10 10 0 0 0 0-20zm-1 17.9A8 8 0 0 1 4.2 10.2L9 15v1a2 2 0 0 0 2 2zm6.9-2.5A2 2 0 0 0 16 16h-1v-3a1 1 0 0 0-1-1H8v-2h2a1 1 0 0 0 1-1V7h2a2 2 0 0 0 2-2v-.4a8 8 0 0 1 2.9 12.8z"/></svg>
          www.KLV.com
        </li>
      </ul>
    </div>
    <div class="edge-rule"></div>
    <div class="edge-band"></div>
  </section>

  <section class="card card--back">
    <div class="brand">
      <span class="brand__mark">KLV</span>
      <span class="brand__sub">Plant Services</span>
    </div>
  </section>
</body>
</html>
```